Visitenkarten und Briefpapier
Zielgruppe
Planung und Realisierung von individuellen und wertbeständigen Kamin- und Ofenlösungen, sowie Fliesen- und Baddesign.
Aufgabenstellung
Wir benötigen ein möglichst schlichtes Design für Visitenkarten, bzw. Briefpapier. Für die Visitenkarten gerne auch Vorschläge mit Prägung, Ausstanzung oder mit Heißfolie. Auch Klappkarten wären denkbar. Das Design soll "das gewisse Etwas haben" und nicht zu verspielt sein.
Die Visitenkarten sind für die Firma KORVA, das Logo von der Ausstellung "raumfunke" soll dezent mit eingebunden werden (bei dem Briefpapier z.B. in der Fußzeile". Die farbliche Gestaltung sollte sich an den Farben des Logos orientieren.
Schriftart für Texte: Century Gothic
Schriftfarbe: RAL 7016
Nur eine Idee: Ich könnte mir auch gut vorstellen, dass die Visitenkarte aus einer Zündholzverpackung (wenn dann aber eine besondere mit nur einem Zündholz oder einem besonders breiten) besteht: http://glimmvelo.de/produkte_briefchen.php

```html
<!DOCTYPE html>
<html lang="de">
<head>
<meta charset="utf-8">
<title>KORVA – Geschäftsausstattung</title>
<link href="https://fonts.googleapis.com/css2?family=Questrial&display=swap" rel="stylesheet">
<style>
:root{
  --bg:#ededed;
  --paper:#f7f7f7;
  --anthracite:#1f2a2e;
  --ink:#383e42;
  --muted:#8a8f93;
  --flame:#e0661c;
  --flame-deep:#c44a10;
  --font:"Questrial","Century Gothic",sans-serif;
}
*{margin:0;padding:0;box-sizing:border-box}
html,body{width:1200px;height:795px;overflow:hidden}
body{background:var(--bg);font-family:var(--font);color:var(--ink);position:relative}
.abs{position:absolute}

/* brand lockup */
.brand{display:flex;flex-direction:column;align-items:flex-start;line-height:1}
.brand-row{display:flex;align-items:center;gap:.12em}
.brand-name{font-weight:400;letter-spacing:.02em;color:var(--ink)}
.brand-dot{width:.22em;height:.22em;border-radius:50%;background:var(--flame)}
.brand-tag{letter-spacing:.02em;color:var(--ink);margin-top:.1em}
.on-dark .brand-name,.on-dark .brand-tag{color:#f2f2f2}

.hero-brand{left:57px;top:66px}
.hero-brand .brand-name{font-size:56px;color:#151515}
.hero-brand .brand-tag{font-size:15px;color:var(--ink)}

.partner{font-family:var(--font);color:var(--muted);letter-spacing:.01em}

/* letterhead */
.letterhead{left:292px;top:99px;width:293px;height:415px;background:var(--paper)}
.lh-head{left:30px;top:22px;width:231px;height:27px;border-bottom:1px solid var(--ink)}
.lh-head .brand-name{font-size:19px}
.lh-head .brand-tag{font-size:5.6px}
.lh-addr{right:2px;top:12px;font-size:4px;color:var(--muted);text-align:right;display:flex;gap:4px;align-items:center}
.lh-addr svg{width:6px;height:8px}
.lh-recipient{left:30px;top:90px;font-size:5px;line-height:7px;color:var(--muted)}
.lh-date{right:32px;top:90px;font-size:5px;color:var(--muted)}
.lh-salute{left:30px;top:145px;font-size:5px;color:var(--ink)}
.lh-body{left:30px;top:162px;width:232px;font-size:5.1px;line-height:7px;color:var(--ink);text-align:justify}
.lh-body p+p{margin-top:4px}
.lh-sign{left:188px;top:288px;font-size:5.6px;color:var(--muted);text-align:center;line-height:9px}
.lh-sign u{text-decoration:underline}
.lh-legal{left:30px;top:345px;font-size:3.3px;line-height:4.3px;color:var(--muted)}
.lh-legal b{color:var(--ink);font-weight:400}
.lh-legal .gap{margin-top:2px}
.lh-contact{right:32px;top:368px;font-size:3.6px;line-height:6px;color:var(--muted);text-align:right}
.lh-web{left:0;width:100%;top:395px;text-align:center;font-size:4px;color:var(--ink)}

/* folder */
.folder{left:635px;top:75px;width:348px;height:443px;background:var(--anthracite)}
.folder-spine{left:8px;top:0;width:1px;height:100%;background:#2c393e}
.folder-brand{left:118px;top:44px}
.folder-brand .brand-name{font-size:38px}
.folder-brand .brand-tag{font-size:10.5px}
.folder-motif{left:140px;top:112px;width:160px;height:318px}
.folder-partner{right:24px;bottom:20px;font-size:9px;color:#9aa1a4}

/* business cards */
.card-front{left:185px;top:551px;width:133px;height:75px;background:var(--anthracite)}
.card-front .brand{left:29px;top:24px}
.card-front .brand-name{font-size:22px}
.card-front .brand-tag{font-size:6.6px}
.card-front .partner{right:7px;bottom:6px;font-size:4px;color:#9aa1a4}

.card-back{left:186px;top:647px;width:134px;height:75px;background:var(--paper)}
.card-back .brand{left:9px;top:7px}
.card-back .brand-name{font-size:13.5px}
.card-back .brand-tag{font-size:3.8px}
.cb-rule{left:0;top:33px;width:120px;height:0;border-top:.8px solid var(--ink)}
.cb-name{right:14px;top:27px;font-size:5.3px;color:var(--ink);text-align:right;line-height:5px}
.cb-role{right:14px;top:34px;font-size:3.3px;color:var(--muted)}
.cb-addr{left:9px;top:59px;font-size:3.6px;line-height:4.3px;color:var(--muted)}
.cb-contact{right:11px;top:56px;font-size:3.6px;line-height:4.3px;color:var(--muted);text-align:right}

/* envelopes */
.env-front{left:353px;top:561px;width:329px;height:157px;background:var(--paper)}
.env-front .brand{left:16px;top:14px}
.env-front .brand-name{font-size:19px}
.env-front .brand-tag{font-size:5.6px}
.env-front .partner{left:16px;bottom:14px;font-size:8px}
.env-addr{right:24px;bottom:12px;font-size:5.8px;line-height:6.4px;color:var(--muted);text-align:right}

.env-back{left:713px;top:561px;width:329px;height:157px;background:var(--paper)}
.env-flap{left:0;top:0;width:329px;height:56px}
.env-back .brand{left:139px;top:16px}
.env-back .brand-name{font-size:14px;color:#6e777b}
.env-back .brand-tag{font-size:3.8px;color:#6e777b}
</style>
</head>
<body>

<div class="abs brand hero-brand">
  <div class="brand-row"><span class="brand-name">KORVA</span><span class="brand-dot"></span></div>
  <span class="brand-tag">kamine · öfen · fliesen</span>
</div>

<!-- letterhead -->
<section class="abs letterhead">
  <div class="abs lh-head">
    <div class="brand">
      <div class="brand-row"><span class="brand-name">KORVA</span></div>
      <span class="brand-tag">kamine · öfen · fliesen</span>
    </div>
    <div class="abs lh-addr">
      <svg viewBox="0 0 6 8"><path d="M3 0a3 3 0 0 1 3 3c0 2-3 5-3 5S0 5 0 3a3 3 0 0 1 3-3z" fill="#383e42"/><circle cx="3" cy="3" r="1.1" fill="#f7f7f7"/></svg>
      <span>Am Lindenhang 12<br>34510 Talbrück</span>
    </div>
  </div>

  <div class="abs lh-recipient">Sr. Tomás Ribera Olmo<br>Director Comercial<br>VENTALIS S.L.<br>c/ Almendro 9, 08290 Cerdanyola</div>
  <div class="abs lh-date">London September 27, 2045</div>
  <div class="abs lh-salute">Dear Costumer,</div>

  <div class="abs lh-body">
    <p>Lorem ipsum dolor sit amet, consectetur adipiscing elit. Nam urna dui, accumsan auctor gravida nec, tempus nec ante. Nam vitae mi et est feugiat interdum. Nam eget tortor ligula consectetur tristique risus. Vivamus quis libero vel odio dictum rhoncus. Donec non metus sed quam posuere vestibulum. Quisque feugiat, mi quis congue egestas, lectus dui rutrum odio, et dignissim justo lorem quis nunc. Duis euismod purus sit amet orci cursus congue. Nulla vitae fermentum ante. Integer interdum massa vitae nisl scelerisque eu vulputate leo malesuada. Nulla in purus eu augue aliquet tempor nec condimentum neque. Nullam sed nulla metus.</p>
    <p>Suspendisse a risus quis risus condimentum gravida a in lacus. Aenean vel ipsum venenatis velit lobortis ultricies a nec risus. In hac habitasse platea dictumst. Aenean gravida rutrum accumsan. Nulla accumsan ullamcorper mauris ac iaculis. Donec volutpat turpis ac porta tincidunt felis neque blandit augue eget pharetra tortor turpis quis metus. Etiam non risus ac est luctus ornare. Vivamus porta, velit quis pharetra pellentesque, urna nisi tempus quam, non eleifend nulla leo vel dui.</p>
    <p>Suspendisse a risus quis risus condimentum gravida a in lacus. Aenean vel ipsum venenatis velit lobortis ultricies a nec risus. In hac habitasse platea dictumst. Aenean gravida rutrum accumsan. Nulla accumsan ullamcorper mauris ac iaculis. Donec volutpat, turpis ac porta tincidunt, felis neque.</p>
  </div>

  <div class="abs lh-sign">Best Regards<br><u>KORVA</u></div>

  <div class="abs lh-legal">
    <b>Geschäftsführer: Jonas Berktal</b><br>
    Amtsgericht Talbrück HRB 4410, USt-IdNr. DE 204518337<br>
    Steuernummer: 027 318 44051
    <div class="gap"><b>Bankverbindung 1</b><br>BIC: TALBDE51XXX<br>IBAN: DE12 5104 0000 0031 7750 20</div>
    <div class="gap"><b>Bankverbindung 2</b><br>BIC: HESSDE66YYY<br>IBAN: DE48 5105 0000 0012 4471 09</div>
  </div>

  <div class="abs lh-contact">05640 / 71 38 20 ☏<br>05640 / 71 38 28 ●<br>info@korva-talbrueck.de ✉</div>
  <div class="abs lh-web">www.korva-talbrueck.de</div>
</section>

<!-- presentation folder -->
<section class="abs folder">
  <div class="abs folder-spine"></div>
  <div class="abs brand folder-brand on-dark">
    <div class="brand-row"><span class="brand-name">KORVA</span></div>
    <span class="brand-tag">kamine · öfen · fliesen</span>
  </div>
  <svg class="abs folder-motif" role="img" aria-label="Large orange flame motif" viewBox="0 0 160 318" preserveAspectRatio="none">
    <defs>
      <linearGradient id="flameFade" x1="0" y1="0" x2="1" y2="1">
        <stop offset="0" stop-color="#e58030" stop-opacity=".85"/>
        <stop offset="1" stop-color="#c44a10" stop-opacity=".85"/>
      </linearGradient>
    </defs>
    <rect width="160" height="318" rx="6" fill="url(#flameFade)"/>
  </svg>
  <span class="abs partner folder-partner">raumfunke</span>
</section>

<!-- business card, front -->
<section class="abs card-front">
  <div class="abs brand on-dark">
    <div class="brand-row"><span class="brand-name">KORVA</span></div>
    <span class="brand-tag">kamine · öfen · fliesen</span>
  </div>
  <span class="abs partner">raumfunke</span>
</section>

<!-- business card, back -->
<section class="abs card-back">
  <div class="abs brand">
    <div class="brand-row"><span class="brand-name">KORVA</span></div>
    <span class="brand-tag">kamine · öfen · fliesen</span>
  </div>
  <div class="abs cb-name">Jonas Berktal</div>
  <div class="abs cb-rule"></div>
  <div class="abs cb-role">Geschäftsführer</div>
  <div class="abs cb-addr">Am Lindenhang 12<br>34510 Talbrück</div>
  <div class="abs cb-contact">05640 / 71 38 20 ☏<br>05640 / 71 38 28 ●<br>info@korva-talbrueck.de ✉</div>
</section>

<!-- envelope, front -->
<section class="abs env-front">
  <div class="abs brand">
    <div class="brand-row"><span class="brand-name">KORVA</span></div>
    <span class="brand-tag">kamine · öfen · fliesen</span>
  </div>
  <span class="abs partner">raumfunke</span>
  <div class="abs env-addr">Am Lindenhang 12<br>34510 Talbrück</div>
</section>

<!-- envelope, back -->
<section class="abs env-back">
  <svg class="abs env-flap" viewBox="0 0 329 56" preserveAspectRatio="none">
    <path d="M0 0H329L322 48Q321 55 313 55H16Q8 55 7 48Z" fill="var(--anthracite)"/>
  </svg>
  <div class="abs brand">
    <div class="brand-row"><span class="brand-name">KORVA</span></div>
    <span class="brand-tag">kamine · öfen · fliesen</span>
  </div>
</section>

</body>
</html>
```